Website Design for a holiday home letting busines

We require a redesign of our present website www.pinebrookstays.com. We want the website to stand out and look professional and clean to make holiday hunters want to book a caravan or lodge holiday with us. Our logo is red however we DO NOT want the website to be red. We want a natural colour scheme.

The final design should communicate that we are a professional company to book with.

On the home page we require;
Overview of company
Photo
Search box for holiday (check in)
Late Deals
Reviews
News

We would like the following pages designed; home page, available dates page, caravans page, content page.

The website should be responsive for smart phones. One website I do like is http://www.verdoliso.be/nl/

Target Market(s)

Families

Industry/Entity Type

Travel

Number of Pages Required

5+ page

Font styles to use
Serif

Requirements
Must have
• The project must be responsive for mobile phones and tablets.
• Ability to search for holiday home holidays
• We want a natural colour scheme.
Nice to have
• A style we like is http://www.verdoliso.be/nl/
Should not have
• Do not use red as a colour for the website. Our logo is red so this is the only time we want this used.

```html
<!DOCTYPE html>
<html lang="en">
<head>
<meta charset="utf-8">
<title>Pinebrook Stays – Private Holiday Rentals</title>
<link href="https://fonts.googleapis.com/css2?family=Roboto:wght@300;400;500;700&display=swap" rel="stylesheet">
<style>
:root{
  --ink:#333;
  --muted:#888;
  --charcoal:#2b2b2b;
  --charcoal-2:#3a3a3a;
  --footer:#444;
  --logo:#c8332b;
  --accent:#5f7a3e;
  --accent-dark:#4a6130;
  --line:#e3e3e3;
  --band:#f2f2f2;
  --white:#fff;
  --slate:#4a5a4e;
  --photo-green:#7d9466;
  --photo-sand:#c9b48f;
  --photo-sky:#a9c1d6;
  --photo-wood:#8a5a3a;
}
*{box-sizing:border-box;margin:0;padding:0}
html,body{width:745px;height:1200px;overflow:hidden}
body{font-family:"Roboto",Arial,sans-serif;color:var(--ink);background:var(--white);font-size:7px;line-height:1.35}
.site{width:745px;height:1200px;position:relative;overflow:hidden}
.wrap{width:640px;margin:0 auto;position:relative}

/* header */
.topbar{height:37px;background:var(--white)}
.topbar .wrap{display:flex;align-items:center;justify-content:space-between;height:37px}
.brand{display:flex;align-items:center;gap:6px;font-weight:700;font-size:13px;color:var(--logo)}
.brand-dot{width:14px;height:14px;border-radius:50%;background:var(--logo)}
.top-contact{display:flex;align-items:center;gap:6px}
.top-contact .phone{text-align:right;font-size:7px;color:var(--muted)}
.top-contact .phone b{display:block;font-size:10px;color:var(--charcoal)}
.round{width:14px;height:14px;border-radius:50%;background:var(--charcoal-2);display:inline-flex}
.nav{height:15px;background:var(--charcoal)}
.nav ul{list-style:none;display:flex;height:15px;align-items:center}
.nav li{color:#ddd;font-size:6.5px;padding:0 8px;height:15px;line-height:15px}
.nav li.active{background:var(--accent);color:var(--white)}

/* hero */
.hero{height:240px;background:radial-gradient(circle at 62% 40%,#4a4a4a 0,#2f2f2f 55%,#262626 100%);position:relative;overflow:hidden}
.hero-arc{position:absolute;left:330px;top:-40px;width:300px;height:300px;border-radius:50%;background:#3a3a3a}
.hero-photo{position:absolute;left:358px;top:-8px;width:244px;height:244px;border-radius:50%;border:4px solid var(--white);background:linear-gradient(160deg,#d9cbb4,#9c7a5a 55%,#6e5540)}
.hero-copy{position:absolute;left:53px;top:56px;color:var(--white);width:200px}
.hero-copy h1{font-size:15px;font-weight:700;margin-bottom:6px}
.hero-copy p{font-size:7px;color:#ddd;margin-bottom:8px}
.btn-ghost{display:inline-block;border:1px solid #bbb;color:#eee;font-size:6px;padding:2px 6px}
.search{position:absolute;left:52px;right:52px;top:200px;height:38px;background:rgba(20,20,20,.85);display:flex;align-items:flex-end;gap:6px;padding:6px 8px}
.search h2{font-size:13px;color:var(--white);font-weight:500;width:50px}
.field{flex:1}
.field span{display:block;color:#bbb;font-size:5.5px;margin-bottom:2px}
.field i{display:block;height:11px;background:var(--white)}
.search-btn{width:16px;height:11px;background:var(--accent);display:flex;align-items:center;justify-content:center}

/* sections */
.section-title{font-size:10px;font-weight:500;color:var(--accent);margin-bottom:7px}
.section-title.center{text-align:center}
.deals{padding:10px 0 0;height:140px}
.cards{display:flex;gap:10px}
.card{flex:1}
.ph{display:block;height:60px}
.card p{font-size:5.5px;color:var(--ink);margin-top:5px}
.card .rule{display:block;width:28px;height:2px;background:var(--accent);margin-top:4px}
.sep{height:1px;background:var(--line);width:640px;margin:0 auto}
.listing{display:flex;gap:14px;padding-top:12px}
.listing .main{width:410px}
.listing .cards .ph{height:50px}
.listing.tall .ph{height:72px}
.side{width:216px}
.panel{border:1px solid var(--line)}
.panel-head{background:var(--slate);color:var(--white);font-size:7px;font-weight:500;padding:4px 6px}
.feed-item{display:flex;gap:5px;padding:4px 6px;border-bottom:1px solid var(--line)}
.feed-item .thumb{width:22px;height:18px;flex:none}
.feed-item p{font-size:5.5px;color:#555}
.feed-item p b{color:var(--slate);display:block}
.tags{padding:6px;background:var(--white)}
.tags h3{font-size:9px;color:var(--accent);font-weight:500;margin-bottom:4px}
.tag-cloud{font-size:6px;color:var(--slate);line-height:1.6}
.tag-cloud span{margin-right:4px}
.tag-cloud .l{font-size:9px}
.tag-cloud .m{font-size:7.5px}

/* reviews */
.reviews{background:var(--band);height:104px;margin-top:30px;padding-top:10px;position:relative}
.review{display:flex;gap:14px;align-items:flex-start;width:520px;margin:0 auto}
.avatar{width:46px;height:46px;border-radius:50%;background:linear-gradient(#c9b9a6,#8e7c68);flex:none}
.review p{font-size:6.5px;color:#666;font-style:italic}
.review .who{color:var(--accent);font-style:normal;margin-top:4px;font-size:6.5px}
.arrow{position:absolute;top:54px}
.arrow.l{left:60px}.arrow.r{right:60px}

/* blog */
.blog{padding-top:20px}
.blog .cards{gap:14px}
.blog .ph{height:72px}
.blog h4{font-size:7px;font-weight:700;margin-top:6px}
.blog p{font-size:6px;color:#666;margin-top:3px}
.btn-small{display:inline-block;margin-top:5px;border:1px solid #bbb;font-size:5.5px;padding:2px 6px;color:#555}

/* footer */
.newsletter{position:absolute;top:1062px;left:0;width:745px;height:28px;background:#555}
.newsletter .wrap{display:flex;align-items:center;justify-content:center;gap:8px;height:28px}
.newsletter h3{color:var(--white);font-size:11px;font-weight:400}
.newsletter i{width:150px;height:13px;background:var(--white);display:block}
.newsletter .go{width:30px;height:13px;background:var(--charcoal);color:#fff;font-size:6px;text-align:center;line-height:13px}
.footer{position:absolute;top:1090px;left:0;width:745px;height:92px;background:var(--footer);color:#ccc}
.footer .wrap{display:flex;gap:20px;padding-top:10px}
.fcol{flex:1}
.fcol h5{font-size:6px;color:var(--white);font-weight:500;margin-bottom:5px;text-transform:uppercase}
.fcol li{list-style:none;font-size:5.5px;margin-bottom:2px}
.fcol .in{height:8px;background:#666;margin-bottom:3px}
.fcol .socials{display:flex;gap:4px;margin-bottom:6px}
.fcol .socials .round{background:#666}
.fcol .cta{display:inline-block;background:var(--accent);color:#fff;font-size:6px;padding:3px 8px}
.bottom{position:absolute;top:1182px;left:0;width:745px;height:18px;background:#333;color:#999;font-size:5.5px}
.bottom .wrap{line-height:18px}
</style>
</head>
<body>
<div class="site">
  <header class="topbar">
    <div class="wrap">
      <div class="brand"><span class="brand-dot"></span>Pinebrook Stays</div>
      <div class="top-contact">
        <div class="phone">www.pinebrookstays.com<b>01632 960 480</b></div>
        <span class="round"></span><span class="round"></span><span class="round"></span>
      </div>
    </div>
  </header>
  <nav class="nav">
    <div class="wrap">
      <ul>
        <li class="active">Home</li><li>News</li><li>Holidays</li><li>Caravans for Hire</li><li>Lodges for Hire</li><li>Availability</li><li>Late Deals</li><li>Park Facilities</li><li>Contact Us</li>
      </ul>
    </div>
  </nav>

  <section class="hero">
    <div class="hero-arc"></div>
    <div class="hero-photo" role="img" aria-label="Photo of a smiling family outdoors on holiday"></div>
    <div class="hero-copy">
      <h1>Private Holiday Rentals</h1>
      <p>Quality Lodge &amp; Caravan Hire at Sandmere Holiday Park. Book online today!</p>
      <span class="btn-ghost">Read More</span>
    </div>
    <form class="search">
      <h2>Search</h2>
      <div class="field"><span>Check in</span><i></i></div>
      <div class="field"><span>Nights</span><i></i></div>
      <div class="field"><span>Type</span><i></i></div>
      <div class="field"><span>Bedrooms</span><i></i></div>
      <div class="field"><span>Guests</span><i></i></div>
      <div class="search-btn"><svg width="7" height="7" viewBox="0 0 10 10"><circle cx="4" cy="4" r="3" fill="none" stroke="#fff" stroke-width="1.5"/><path d="M6.5 6.5L9 9" stroke="#fff" stroke-width="1.5"/></svg></div>
    </form>
  </section>

  <section class="deals wrap">
    <h2 class="section-title">Latest Deals</h2>
    <div class="cards">
      <div class="card"><span class="ph" role="img" aria-label="Photo of a bright lodge interior" style="background:linear-gradient(#d8cfc2,#a8917a)"></span><p>Cosy lodge for six near the lake, short breaks</p><span class="rule"></span></div>
      <div class="card"><span class="ph" role="img" aria-label="Photo of a static caravan on grass" style="background:linear-gradient(var(--photo-sky),#e6e6e6 60%,var(--photo-green))"></span><p>Modern caravan with deck, weekend savings</p><span class="rule"></span></div>
      <div class="card"><span class="ph" role="img" aria-label="Photo of a wooden lodge among trees" style="background:linear-gradient(#b7c9a0,var(--photo-wood))"></span><p>Woodland lodge with hot tub, late deal price</p><span class="rule"></span></div>
      <div class="card"><span class="ph" role="img" aria-label="Photo of a caravan row on a park" style="background:linear-gradient(var(--photo-sky),#dcdcdc 55%,var(--photo-green))"></span><p>Family caravan near the beach, midweek offer</p><span class="rule"></span></div>
      <div class="card"><span class="ph" role="img" aria-label="Photo of a timber lodge exterior" style="background:linear-gradient(#9fb58a,#7a4e30)"></span><p>Timber lodge with garden, summer discount</p><span class="rule"></span></div>
    </div>
  </section>

  <div class="sep"></div>

  <div class="wrap">
    <div class="listing">
      <div class="main">
        <h2 class="section-title">List of Caravans</h2>
        <div class="cards">
          <div class="card"><span class="ph" role="img" aria-label="Photo of a white caravan" style="background:linear-gradient(var(--photo-sky),#eee 55%,var(--photo-green))"></span><p>Three bedroom caravan with sea view deck</p></div>
          <div class="card"><span class="ph" role="img" aria-label="Photo of a touring caravan" style="background:linear-gradient(#b9cde0,#e2e2e2 55%,#8aa070)"></span><p>Spacious caravan close to the pool area</p></div>
          <div class="card"><span class="ph" role="img" aria-label="Photo of a caravan beside a lawn" style="background:linear-gradient(#c5d6e6,#d9d2c4 55%,var(--photo-green))"></span><p>Two bedroom caravan, ideal for families</p></div>
          <div class="card"><span class="ph" role="img" aria-label="Photo of a caravan on a green pitch" style="background:linear-gradient(#a9c1d6,#7f9a66)"></span><p>Pet friendly caravan with private parking</p></div>
        </div>
      </div>
      <aside class="side">
        <div class="panel">
          <div class="panel-head">Social Deals</div>
          <div class="feed-item"><span class="thumb" role="img" aria-label="Small lodge photo" style="background:var(--photo-wood)"></span><p><b>Pinebrook Stays</b>Three nights for the price of two this spring</p></div>
          <div class="feed-item"><span class="thumb" role="img" aria-label="Small caravan photo" style="background:var(--photo-sky)"></span><p><b>Pinebrook Stays</b>New lodge added with lake views and hot tub</p></div>
          <div class="feed-item"><span class="thumb" role="img" aria-label="Small park photo" style="background:var(--photo-green)"></span><p><b>Pinebrook Stays</b>Half term dates still free, book early now</p></div>
          <div class="feed-item"><span class="thumb" role="img" aria-label="Small beach photo" style="background:var(--photo-sand)"></span><p><b>Pinebrook Stays</b>Summer weeks now open for online booking</p></div>
        </div>
      </aside>
    </div>

    <div class="listing tall" style="padding-top:18px">
      <div class="main">
        <h2 class="section-title">List of Caravans</h2>
        <div class="cards">
          <div class="card"><span class="ph" role="img" aria-label="Photo of a lodge bedroom" style="background:linear-gradient(#c7a98a,#7c5536)"></span><p>Lodge with double bedroom and ensuite bath</p></div>
          <div class="card"><span class="ph" role="img" aria-label="Photo of a lodge in a forest" style="background:linear-gradient(#8fa77a,#5d4a32)"></span><p>Forest lodge with veranda and fire pit</p></div>
          <div class="card"><span class="ph" role="img" aria-label="Photo of a lodge by the water" style="background:linear-gradient(#a8bfae,#6f7f55)"></span><p>Waterside lodge with decking and hot tub</p></div>
        </div>
      </div>
      <aside class="side" style="padding-top:6px">
        <div class="panel tags">
          <h3>Tags</h3>
          <div class="tag-cloud"><span class="l">Lodges</span><span>beach</span><span class="m">Caravans</span><span>pets</span><span>hot tub</span><span class="m">Family</span><span>late deals</span><span>park</span><span class="l">Holidays</span><span>pool</span><span>weekend</span></div>
        </div>
      </aside>
    </div>
  </div>

  <section class="reviews">
    <h2 class="section-title center">Latest reviews</h2>
    <svg class="arrow l" width="6" height="10" viewBox="0 0 6 10"><path d="M5 1L1 5l4 4" fill="none" stroke="#999" stroke-width="1.2"/></svg>
    <div class="review">
      <div class="avatar" role="img" aria-label="Guest profile photo"></div>
      <div>
        <p>"A lovely clean caravan in a quiet spot of the park. The children loved the pool and the beach walks, and booking online was quick and simple. We will certainly be back next summer with the whole family."</p>
        <p class="who">Jane Whitfield</p>
      </div>
    </div>
    <svg class="arrow r" width="6" height="10" viewBox="0 0 6 10"><path d="M1 1l4 4-4 4" fill="none" stroke="#999" stroke-width="1.2"/></svg>
  </section>

  <section class="blog wrap">
    <h2 class="section-title center">Blog</h2>
    <div class="cards">
      <article class="card"><span class="ph" role="img" aria-label="Photo of a bright living room" style="background:linear-gradient(#eee,#c9c2b8)"></span><h4>Five tips for a relaxing lodge break with kids</h4><p>Plan your days, pack light and make time for the park trails.</p><span class="btn-small">Read more</span></article>
      <article class="card"><span class="ph" role="img" aria-label="Photo of a log cabin in woods" style="background:linear-gradient(#9ab384,#6b4a2e)"></span><h4>New woodland lodges open for the summer season</h4><p>Our newest lodges bring space, comfort and forest views.</p><span class="btn-small">Read more</span></article>
    </div>
  </section>

  <section class="newsletter">
    <div class="wrap"><h3>Newsletter Subscribe</h3><i></i><span class="go">Send</span></div>
  </section>
  <footer class="footer">
    <div class="wrap">
      <div class="fcol"><h5>Search for Holidays</h5><div class="in"></div><div class="in"></div><div class="in" style="width:50%"></div></div>
      <div class="fcol"><h5>Quick Links</h5><ul><li>Home</li><li>Holidays</li><li>Caravans</li><li>Lodges</li><li>Contact</li></ul></div>
      <div class="fcol"><h5>Pages</h5><ul><li>Late Deals</li><li>Availability</li><li>Park Facilities</li><li>News</li></ul></div>
      <div class="fcol"><h5>Contact</h5><ul><li>Sandmere Holiday Park</li><li>01632 960 480</li><li>hello@pinebrookstays.com</li></ul></div>
      <div class="fcol"><h5>Get our offers</h5><div class="socials"><span class="round"></span><span class="round"></span><span class="round"></span><span class="round"></span></div><span class="cta">Book Now</span></div>
    </div>
  </footer>
  <div class="bottom"><div class="wrap">Copyright © 2015 Pinebrook Stays. All rights reserved.</div></div>
</div>
</body>
</html>
```